"Vine Hollow Excursions" is a top notch Santa Barbara County Wine Tour company.

We provide scenic, boutique and custom wine tours. I need the card to be clean and classy. I will provide our logo. I would like the logo to cover the back side of the card as an option and would like to see a couple color options other then our signature green and gold. I would like to see some creative options and let the designers come up with options.
I need cards for myself and my team. The final design should communicate "An authentic and boutique wine tour experience"
Please use my website for reference www.vinehollowexcursions.example

Target Market(s)

We have a wide range of clients from millennials to baby boomers

Industry/Entity Type

Tour

Contact Information for Business Card

Contact info:
Dale Morton
805-219-6384
info@vinehollowexcursions.example
vinehollowexcursions.example

Colors

Designer to choose colors to be used in the design.

Requirements
Must have
• my logo
Nice to have
• *I would like to have the backside side with the logo and the company statement
• "An authentic and boutique wine tour experience" as an option.
• *I would also like to see what the designers can create!
• *I would like to see an option that incorporates or social: instagram, yelp, trip advisor
Should not have
• I do not want it too busy.

```html
<!DOCTYPE html>
<html lang="en">
<head>
<meta charset="utf-8">
<title>Vine Hollow Excursions – Business Card</title>
<link rel="stylesheet" href="https://fonts.googleapis.com/css2?family=Cinzel:wght@400;600&family=Open+Sans:wght@400;600;700&display=swap">
<style>
  :root {
    --green: #1f6b3c;
    --green-soft: #d9e6dc;
    --gold: #a8875a;
    --paper: #ffffff;
    --ink: #2f2f2f;
    --backdrop: #e6e7e6;
    --mark-tint: rgba(255,255,255,0.85);
    --icon-one: #8a6a4c;
    --icon-two: #4a8a2c;
    --icon-three: #c8282a;
  }
  * { box-sizing: border-box; margin: 0; padding: 0; }
  html, body { width: 1200px; height: 960px; overflow: hidden; }
  body {
    background: var(--backdrop);
    position: relative;
    font-family: "Open Sans", Arial, sans-serif;
  }
  .card {
    position: absolute;
    left: 240px;
    width: 720px;
    height: 411px;
    overflow: hidden;
    box-shadow: 0 6px 18px rgba(0,0,0,0.18);
  }

  /* Back side */
  .card-back {
    top: 31px;
    background: var(--green);
    color: var(--paper);
    display: flex;
    flex-direction: column;
    align-items: center;
    justify-content: center;
    text-align: center;
  }
  .card-back .brand-mark {
    width: 64px;
    height: 64px;
    background: var(--mark-tint);
    margin-bottom: 18px;
  }
  .card-back .brand-name {
    font-family: "Cinzel", Georgia, serif;
    font-weight: 400;
    font-size: 40px;
    letter-spacing: 1px;
    line-height: 1.1;
  }
  .card-back .brand-region {
    font-family: "Cinzel", Georgia, serif;
    font-size: 13px;
    letter-spacing: 6px;
    margin-top: 10px;
  }
  .card-back .brand-tagline {
    font-weight: 700;
    font-size: 16px;
    margin-top: 6px;
  }

  /* Front side */
  .card-front {
    top: 478px;
    background: var(--paper);
  }
  .illustration {
    position: absolute;
    left: 0;
    top: 110px;
    width: 470px;
    height: 251px;
    background: linear-gradient(180deg, var(--paper) 0%, var(--green-soft) 45%, var(--green) 100%);
  }
  .web-band {
    position: absolute;
    left: 0;
    right: 0;
    bottom: 0;
    height: 50px;
    background: var(--green);
    display: flex;
    align-items: center;
    justify-content: center;
    color: var(--paper);
    font-size: 18px;
    font-weight: 600;
    letter-spacing: 3px;
  }
  .social-links {
    position: absolute;
    top: 24px;
    left: 28px;
    display: flex;
    gap: 6px;
  }
  .social-links span {
    width: 30px;
    height: 30px;
    border-radius: 5px;
    display: block;
  }
  .social-links .social-one { background: var(--icon-one); }
  .social-links .social-two { background: var(--icon-two); }
  .social-links .social-three { background: var(--icon-three); }

  .identity {
    position: absolute;
    right: 34px;
    top: 96px;
    text-align: right;
  }
  .identity .brand-name {
    font-family: "Cinzel", Georgia, serif;
    font-size: 27px;
    color: var(--gold);
    line-height: 1;
  }
  .identity .brand-region {
    font-family: "Cinzel", Georgia, serif;
    font-size: 10px;
    letter-spacing: 4px;
    color: var(--gold);
    margin-top: 5px;
  }
  .identity .person-name {
    font-family: "Cinzel", Georgia, serif;
    font-weight: 600;
    font-size: 27px;
    color: var(--green);
    margin-top: 22px;
  }
  .contact-list {
    list-style: none;
    margin-top: 6px;
    font-size: 15px;
    color: var(--ink);
  }
  .contact-list li {
    display: flex;
    justify-content: flex-end;
    align-items: center;
    gap: 8px;
    line-height: 24px;
  }
  .contact-list svg { width: 15px; height: 15px; fill: var(--green); }
</style>
</head>
<body>

<section class="card card-back">
  <div class="brand-mark"></div>
  <div class="brand-name">Vine Hollow Excursions</div>
  <div class="brand-region">SANTA BARBARA COUNTY</div>
  <div class="brand-tagline">An authentic &amp; boutique wine tour experience</div>
</section>

<section class="card card-front">
  <div class="illustration" role="img" aria-label="Illustration of a sunburst rising over green mountain ridges"></div>

  <div class="social-links">
    <span class="social-one"></span>
    <span class="social-two"></span>
    <span class="social-three"></span>
  </div>

  <div class="identity">
    <div class="brand-name">Vine Hollow Excursions</div>
    <div class="brand-region">SANTA BARBARA COUNTY</div>
    <div class="person-name">DALE MORTON</div>
    <ul class="contact-list">
      <li>805-219-6384
        <svg viewBox="0 0 24 24"><path d="M6.6 10.8c1.4 2.8 3.8 5.1 6.6 6.6l2.2-2.2c.3-.3.7-.4 1-.2 1.1.4 2.3.6 3.6.6.6 0 1 .4 1 1V20c0 .6-.4 1-1 1C10.6 21 3 13.4 3 4c0-.6.4-1 1-1h3.5c.6 0 1 .4 1 1 0 1.3.2 2.5.6 3.6.1.3 0 .7-.2 1L6.6 10.8z"/></svg>
      </li>
      <li>info@vinehollowexcursions.example
        <svg viewBox="0 0 24 24"><path d="M2 5h20v14H2z M4 7v.4l8 5.2 8-5.2V7z" fill-rule="evenodd"/></svg>
      </li>
    </ul>
  </div>

  <div class="web-band">www.vinehollowexcursions.example</div>
</section>

</body>
</html>
```